Design a large parking banner – mandatory ticket validation in the shop

Banner Size:
548 cm (width) x 154 cm (height)
Note: The banner will be placed in a metal frame at our parking lot entrance, fully visible to every incoming truck driver. The message must be easy to read from a distance.
Goal of the Banner:
To inform all truck drivers that they must validate their entry ticket inside the shop, even if they are parking for a short time.
The message must be displayed in multiple languages for international drivers.
Mandatory Content:
Main message – in multiple languages (clearly separated or stacked):
Dutch (NL): Vergeet je ticket niet te valideren in de shop – verplicht, ook bij kort parkeren!
French (FR): N'oubliez pas de valider votre ticket à la boutique – obligatoire, même pour un court arrêt !
English (EN): Don't forget to validate your entry ticket in the shop – mandatory, even for short stops!
German (DE): Vergessen Sie nicht, Ihr Einfahrticket im Shop zu entwerten – Pflicht, auch bei kurzem Parken!
Polish (PL): Nie zapomnij zatwierdzić biletu w sklepie – obowiązkowe, nawet przy krótkim postoju!
Romanian (RO): Nu uitați să validați biletul în magazin – obligatoriu, chiar și pentru opriri scurte!
You can include more languages if space allows, but these are essential.
Opening Hours Block (in one section below):
Shop Opening Hours
Mon – Fri: 05:30 – 22:00
Sat & Sun: 08:00 – 22:00
Style & Branding:
The design must match the visual identity of Haulport 41Ter
Please refer to the attached photos of existing parking signage for guidance on colors, typography, and layout style
Our logo (attached) must be clearly visible and professionally integrated
Feel free to use icons or pictograms to visually support the message (e.g., ticket, truck, arrow)
Readability is key – large, bold text and high contrast colors that are visible from a distance
Target Audience:
International truck drivers – people who need fast, clear communication. Not everyone speaks the local language, so visual clarity and multilingual messaging are critical.
File Requirements:
Print-ready file (PDF or EPS) – 300 dpi at 1:10 scale
Include 5 cm bleed on all sides
Provide open source files if possible (AI or PSD)

```html
<!DOCTYPE html>
<html lang="en">
<head>
<meta charset="utf-8">
<title>Haulport 41Ter – Entry Ticket Validation Banner</title>
<link rel="stylesheet" href="https://fonts.googleapis.com/css2?family=Barlow+Condensed:ital,wght@1,800&family=Oswald:wght@500;600;700&display=swap">
<style>
  :root {
    --stage: #5b7d9c;
    --navy: #1f2468;
    --navy-deep: #171b52;
    --white: #f4f4f6;
    --gold: #f2b21a;
    --badge: #1b80d2;
    --red: #d7252d;
    --green: #1f9a44;
  }
  * { margin: 0; padding: 0; box-sizing: border-box; }
  html, body { width: 1200px; height: 615px; overflow: hidden; }
  body {
    background: var(--stage);
    font-family: "Oswald", "Arial Narrow", sans-serif;
    position: relative;
  }
  .banner {
    position: absolute;
    left: 15px; top: 138px;
    width: 1170px; height: 339px;
    background: radial-gradient(ellipse at 45% 35%, #2a3080 0%, var(--navy) 45%, var(--navy-deep) 100%);
    overflow: hidden;
    color: var(--white);
  }
  .headline {
    position: absolute;
    left: 30px; top: 26px;
    font-family: "Barlow Condensed", "Arial Narrow", sans-serif;
    font-style: italic;
    font-weight: 800;
    font-variant: small-caps;
    font-size: 66px;
    line-height: 63px;
    letter-spacing: -1px;
    transform: scaleX(0.84);
    transform-origin: left top;
    white-space: nowrap;
  }
  .headline .stress { color: var(--gold); display: block; }
  .lang {
    position: absolute;
    display: flex;
    gap: 11px;
  }
  .lang-code {
    flex: none;
    width: 35px; height: 35px;
    margin-top: 3px;
    background: var(--badge);
    border-radius: 3px;
    font-weight: 600;
    font-size: 23px;
    line-height: 35px;
    text-align: center;
    color: var(--white);
  }
  .lang-text {
    font-weight: 600;
    font-size: 29px;
    line-height: 35px;
    white-space: nowrap;
  }
  .lang-text .stress { color: var(--gold); }
  .lang--nl { left: 351px; top: 21px; }
  .lang--fr { left: 351px; top: 107px; }
  .lang--de { left: 637px; top: 21px; }
  .lang--ro { left: 637px; top: 107px; }
  .lang--pl { left: 952px; top: 21px; }
  .rule {
    position: absolute;
    left: 24px; top: 235px;
    width: 876px; height: 3px;
    background: var(--red);
  }
  .steps {
    position: absolute;
    left: 32px; top: 261px;
    height: 62px;
    display: flex;
    align-items: center;
  }
  .step-truck { width: 88px; height: 58px; }
  .step-arrow { width: 44px; height: 30px; margin: 0 22px 0 20px; }
  .step-arrow--second { margin: 0 27px 0 20px; }
  .step-ticket {
    width: 81px; height: 53px;
    background: var(--white);
    border-radius: 8px;
    display: flex; align-items: center; justify-content: center;
  }
  .step-ticket span {
    display: block;
    border: 2px solid var(--navy);
    border-radius: 5px;
    padding: 0 5px;
    color: var(--navy);
    font-weight: 700;
    font-size: 19px;
    line-height: 25px;
  }
  .step-shop { width: 57px; height: 56px; }
  .hours-label {
    position: absolute;
    left: 452px; top: 262px;
    font-weight: 700;
    font-size: 28px;
    line-height: 31px;
  }
  .hours-label span { display: block; }
  .hours-label .spaced { letter-spacing: 5px; }
  .hours-divider {
    position: absolute;
    left: 568px; top: 256px;
    width: 2px; height: 72px;
    background: var(--white);
  }
  .hours-list {
    position: absolute;
    left: 586px; top: 258px;
    font-weight: 600;
    font-size: 32px;
    line-height: 34px;
    white-space: nowrap;
  }
  .brand {
    position: absolute;
    left: 932px; top: 272px;
    display: flex;
    align-items: center;
    gap: 8px;
  }
  .brand-mark {
    flex: none;
    width: 20px; height: 20px;
    background: var(--badge);
  }
  .brand-name {
    font-weight: 700;
    font-size: 26px;
    line-height: 32px;
    color: var(--white);
    white-space: nowrap;
  }
</style>
</head>
<body>
  <main class="banner">
    <h1 class="headline">
      <span>Entry Ticket</span><br>
      <span>Validation,</span>
      <span class="stress">Mandatory</span>
    </h1>

    <div class="lang lang--nl">
      <span class="lang-code">NL</span>
      <p class="lang-text">Toegangskaart<br>Validatie,<span class="stress">verplicht</span></p>
    </div>
    <div class="lang lang--fr">
      <span class="lang-code">FR</span>
      <p class="lang-text">Billet D'entrée<br>Validation,<br><span class="stress">Obligatoire</span></p>
    </div>
    <div class="lang lang--de">
      <span class="lang-code">DE</span>
      <p class="lang-text">Eintrittskarte<br>Validierung, <span class="stress">Pflichtig</span></p>
    </div>
    <div class="lang lang--ro">
      <span class="lang-code">RO</span>
      <p class="lang-text">Validarea Biletului<br>De Intrare<br><span class="stress">Obligatorie</span></p>
    </div>
    <div class="lang lang--pl">
      <span class="lang-code">PL</span>
      <p class="lang-text">Bilet Wstępu<br>Walidacja,<br><span class="stress">Obowiązkowy</span></p>
    </div>

    <div class="rule"></div>

    <div class="steps">
      <svg class="step-truck" viewBox="0 0 88 58" aria-label="Truck">
        <rect x="0" y="0" width="50" height="40" fill="var(--green)"/>
        <path d="M54 13 H76 Q82 13 85 20 L88 30 V48 H54 Z" fill="var(--green)"/>
        <rect x="60" y="18" width="16" height="11" rx="2" fill="var(--navy)"/>
        <rect x="0" y="43" width="88" height="5" fill="var(--green)"/>
        <circle cx="19" cy="48" r="9" fill="var(--green)" stroke="var(--navy)" stroke-width="3"/>
        <circle cx="64" cy="48" r="9" fill="var(--green)" stroke="var(--navy)" stroke-width="3"/>
      </svg>
      <svg class="step-arrow" viewBox="0 0 44 30" aria-hidden="true">
        <path d="M3 15 H38 M26 4 L39 15 L26 26" fill="none" stroke="var(--white)" stroke-width="6" stroke-linecap="round" stroke-linejoin="round"/>
      </svg>
      <div class="step-ticket"><span>TICKET</span></div>
      <svg class="step-arrow step-arrow--second" viewBox="0 0 44 30" aria-hidden="true">
        <path d="M3 15 H38 M26 4 L39 15 L26 26" fill="none" stroke="var(--white)" stroke-width="6" stroke-linecap="round" stroke-linejoin="round"/>
      </svg>
      <svg class="step-shop" viewBox="0 0 57 56" aria-label="Shop">
        <rect x="0" y="0" width="57" height="13" fill="var(--gold)"/>
        <text x="28.5" y="10.5" text-anchor="middle" font-family="Oswald, sans-serif" font-weight="600" font-size="11" fill="var(--navy)">SHOP</text>
        <rect x="0" y="17" width="57" height="39" fill="var(--gold)"/>
        <rect x="10" y="31" width="10" height="9" fill="var(--navy)"/>
        <rect x="33" y="28" width="14" height="28" fill="var(--navy)"/>
      </svg>
    </div>

    <p class="hours-label"><span>OPENING</span><span class="spaced">HOURS</span></p>
    <div class="hours-divider"></div>
    <p class="hours-list">Mon - Fri: 05:30 - 22:00<br>Sat &amp; Sun: 08:00 - 22:00</p>

    <div class="brand">
      <span class="brand-mark"></span>
      <span class="brand-name">HAULPORT 41TER</span>
    </div>
  </main>
</body>
</html>
```